Ridgeline Journeys business card

please see website
www.ridgelinejourneys.comau

info needed on card
Curtis Halvey
Ph
email
Adventure Riding GPS trails

please use my logo and colours off my site

Curtis Halvey
curtis@ridgelinejourneys.com

```html
<!DOCTYPE html>
<html lang="en">
<head>
<meta charset="utf-8">
<title>Ridgeline Journeys – Business Card</title>
<link rel="stylesheet" href="https://fonts.googleapis.com/css2?family=Open+Sans:ital,wght@0,400;0,600;0,700;1,400;1,600&display=swap">
<style>
  :root {
    --backdrop: #4a4a4a;
    --card-light: #f6f6f6;
    --card-dark: #000000;
    --band: #0a0a0a;
    --accent: #f2e21a;
    --ink: #111111;
    --text: #3c3c3c;
    --muted: #555555;
    --light: #ffffff;
  }
  * { box-sizing: border-box; margin: 0; padding: 0; }
  html, body { width: 1200px; height: 750px; overflow: hidden; }
  body {
    background: var(--backdrop);
    font-family: "Open Sans", Arial, sans-serif;
    position: relative;
  }
  .card {
    position: absolute;
    left: 371px;
    width: 461px;
    height: 262px;
    overflow: hidden;
  }
  .card--front { top: 99px; background: var(--card-light); }
  .card--back { top: 381px; background: var(--card-dark); }

  .brand {
    position: absolute;
    left: 25px;
    top: 30px;
    display: flex;
    align-items: center;
    gap: 16px;
  }
  .brand__dot {
    width: 62px;
    height: 62px;
    border-radius: 50%;
    background: var(--accent);
  }
  .brand__name {
    font-weight: 700;
    font-size: 22px;
    line-height: 25px;
    color: var(--ink);
    text-transform: uppercase;
  }

  .name-band {
    position: absolute;
    left: 0;
    top: 130px;
    width: 100%;
    height: 52px;
    background: var(--band);
    border-top: 2px solid var(--accent);
    border-bottom: 2px solid var(--accent);
    display: flex;
    align-items: center;
    padding-left: 23px;
  }
  .name-band__name {
    color: var(--accent);
    font-weight: 600;
    font-size: 16.5px;
  }

  .contact {
    position: absolute;
    left: 24px;
    top: 196px;
    list-style: none;
  }
  .contact__item {
    display: flex;
    align-items: center;
    height: 18.5px;
    font-size: 10.5px;
    color: var(--text);
  }
  .contact__icon { width: 12px; height: 12px; margin-right: 6px; fill: var(--ink); }

  .tagline {
    position: absolute;
    right: 24px;
    top: 232px;
    font-style: italic;
    font-weight: 600;
    font-size: 12px;
    color: var(--muted);
  }

  .back-brand {
    position: absolute;
    left: 0;
    top: 66px;
    width: 100%;
    display: flex;
    flex-direction: column;
    align-items: center;
    gap: 14px;
  }
  .back-brand__dot {
    width: 78px;
    height: 78px;
    border-radius: 50%;
    background: var(--accent);
  }
  .back-brand__name {
    font-weight: 700;
    font-size: 18px;
    color: var(--light);
    text-transform: uppercase;
  }
  .back-url {
    position: absolute;
    left: 0;
    top: 216px;
    width: 100%;
    text-align: center;
    font-style: italic;
    font-size: 11px;
    color: var(--accent);
  }
</style>
</head>
<body>
  <section class="card card--front" aria-label="Card front">
    <div class="brand">
      <span class="brand__dot"></span>
      <span class="brand__name">Ridgeline<br>Journeys</span>
    </div>

    <div class="name-band">
      <span class="name-band__name">Curtis Halvey</span>
    </div>

    <ul class="contact">
      <li class="contact__item">
        <svg class="contact__icon" viewBox="0 0 24 24" aria-hidden="true"><path d="M6.6 10.8c1.4 2.8 3.8 5.1 6.6 6.6l2.2-2.2c.3-.3.7-.4 1-.2 1.1.4 2.3.6 3.6.6.6 0 1 .4 1 1V20c0 .6-.4 1-1 1C10.6 21 3 13.4 3 4c0-.6.4-1 1-1h3.5c.6 0 1 .4 1 1 0 1.3.2 2.5.6 3.6.1.3 0 .7-.2 1z"/></svg>
        604 218 4470
      </li>
      <li class="contact__item">
        <svg class="contact__icon" viewBox="0 0 24 24" aria-hidden="true"><path d="M2 5h20v14H2z M2 5l10 8 10-8" fill="none" stroke="#111" stroke-width="0"/><path d="M2 5h20l-10 8z"/><path d="M2 7l10 8 10-8v12H2z"/></svg>
        curtis@ridgelinejourneys.com
      </li>
      <li class="contact__item">
        <svg class="contact__icon" viewBox="0 0 24 24" aria-hidden="true"><circle cx="12" cy="12" r="10"/><path d="M12 3.5a8.5 8.5 0 0 0-6 2.5l2 2 1 3 3 1-1 3 2 3 .5 2.4A8.5 8.5 0 0 0 20 9l-3-1-2-3z" fill="#f6f6f6"/></svg>
        www.ridgelinejourneys.com.au
      </li>
    </ul>

    <p class="tagline">Adventure Riding GPS trails</p>
  </section>

  <section class="card card--back" aria-label="Card back">
    <div class="back-brand">
      <span class="back-brand__dot"></span>
      <span class="back-brand__name">Ridgeline Journeys</span>
    </div>
    <p class="back-url">www.ridgelinejourneys.com.au</p>
  </section>
</body>
</html>
```